I have a logo and need to design the business card and stationery.
Updates

The uploaded logo image named as GREYMARSH CONSTRUCTION which is to be replaced to GREYMARSH CONTRACTS. Kindly add below details and submit the designs- Company name- Greymarsh Engineering Contracts LLP Name & Post- Kelvan Joshi (Designated Partner) Address- Block No.317, Wing C, Tulvo Trade Court, Manek Pural Road, Ruparel Industrial Estate, Goregaon(E), Mumbai - 400 063 Contact- +91 97415 60382 Email- kelvanjoshi@mailbrook.example Website- www.greymarshcontracts.example Contact for Letterhead- +91-22-28754193

Hi Tovin Rahul, We are liking your Design #28860835. We have suggested some changes which are mentioned in feedback. Kindly revert with it asap to finalize this design.

Colors

Designer to choose colors to be used in the design.

```html
<!DOCTYPE html>
<html lang="en">
<head>
<meta charset="utf-8">
<title>Greymarsh Contracts – Stationery</title>
<link href="https://fonts.googleapis.com/css2?family=Didact+Gothic&display=swap" rel="stylesheet">
<style>
  :root {
    --bg: #3b3b3b;
    --ink-dark: #333333;
    --paper: #ffffff;
    --text: #4a4a4a;
    --mark: #5f5f5f;
    --soft: #ececec;
  }
  * { margin: 0; padding: 0; box-sizing: border-box; }
  html, body { width: 1200px; height: 800px; overflow: hidden; }
  body {
    background: var(--bg);
    font-family: "Didact Gothic", "Century Gothic", sans-serif;
    color: var(--text);
    position: relative;
  }
  .piece { position: absolute; background: var(--paper); }
  .wordmark { text-align: center; line-height: 1; }
  .wordmark .name { display: block; letter-spacing: 0.04em; }
  .wordmark .sub { display: block; letter-spacing: 0.42em; margin-top: 1px; }
  .mark-square { position: absolute; background: var(--mark); }
  .icon { width: 1em; height: 1em; vertical-align: -0.12em; margin-right: 0.35em; fill: currentColor; }

  /* Business card front */
  .card-front { left: 99px; top: 56px; width: 206px; height: 124px; }
  .card-front .panel-light { position: absolute; left: 0; top: 0; width: 95px; height: 124px; background: var(--paper); }
  .card-front .panel-light .mark-square { left: 11px; top: 21px; width: 80px; height: 80px; }
  .card-front .panel-dark { position: absolute; left: 95px; top: 0; width: 111px; height: 124px; background: var(--ink-dark); color: var(--paper); padding-left: 4px; }
  .card-front .wordmark { position: absolute; left: 4px; top: 21px; width: 85px; color: var(--paper); }
  .card-front .wordmark .name { font-size: 8.6px; }
  .card-front .wordmark .sub { font-size: 4.6px; }
  .card-front .person { position: absolute; left: 4px; top: 50px; font-size: 8.6px; }
  .card-front .role { position: absolute; left: 4px; top: 61px; font-size: 4.6px; }
  .card-front .contacts { position: absolute; left: 4px; top: 81px; list-style: none; font-size: 4.8px; line-height: 7.8px; }

  /* Business card back */
  .card-back { left: 371px; top: 56px; width: 205px; height: 124px; background: var(--ink-dark); }
  .card-back .mark-square { left: 82px; top: 41px; width: 42px; height: 42px; background: var(--paper); }
  .card-back .address-band { position: absolute; left: 0; top: 96px; width: 100%; height: 14px; background: var(--paper); color: #222; font-size: 4.8px; line-height: 6px; text-align: center; padding-top: 1px; }

  /* Envelope back */
  .envelope-back { left: 99px; top: 231px; width: 477px; height: 240px; }
  .envelope-back .flap { position: absolute; left: 0; top: 0; width: 100%; height: 56px; background: var(--ink-dark); border-radius: 0 0 22px 22px; }
  .envelope-back .wordmark { position: absolute; left: 0; right: 0; top: 19px; color: var(--paper); }
  .envelope-back .wordmark .name { font-size: 12.5px; }
  .envelope-back .wordmark .sub { font-size: 6.5px; }

  /* Envelope front */
  .envelope-front { left: 99px; top: 504px; width: 477px; height: 240px; }
  .envelope-front .stripe { position: absolute; left: 0; top: 0; width: 15px; height: 100%; background: var(--ink-dark); }
  .envelope-front .mark-square { left: 61px; top: 15px; width: 35px; height: 35px; }
  .envelope-front .wordmark { position: absolute; left: 20px; width: 117px; top: 56px; color: var(--ink-dark); }
  .envelope-front .wordmark .name { font-size: 12px; }
  .envelope-front .wordmark .sub { font-size: 6.4px; }
  .envelope-front .address { position: absolute; left: 21px; top: 195px; font-size: 6.2px; line-height: 9.2px; color: var(--text); display: flex; }
  .envelope-front .address .icon { margin-top: 1px; }

  /* Letterhead */
  .letterhead { left: 611px; top: 56px; width: 491px; height: 689px; }
  .letterhead .stripe { position: absolute; left: 0; top: 0; width: 26px; height: 100%; background: var(--ink-dark); }
  .letterhead .mark-square { left: 88px; top: 47px; width: 37px; height: 37px; }
  .letterhead .wordmark { position: absolute; left: 47px; width: 118px; top: 90px; color: var(--ink-dark); }
  .letterhead .wordmark .name { font-size: 12px; }
  .letterhead .wordmark .sub { font-size: 6.4px; }
  .letterhead .address { position: absolute; left: 319px; top: 72px; font-size: 6.6px; line-height: 10px; display: flex; }
  .letterhead .address .icon { margin-top: 1px; }
  .letterhead .greeting { position: absolute; left: 47px; top: 174px; font-size: 12px; color: #3d3d3d; }
  .letterhead .body { position: absolute; left: 47px; top: 200px; width: 414px; font-size: 8.5px; line-height: 9.65px; text-align: justify; }
  .letterhead .body p { margin-bottom: 10px; }
  .letterhead .body p.tight { margin-bottom: 0; }
  .letterhead .body p.gap { margin-top: 19px; }
  .letterhead .body p.gap2 { margin-top: 10px; }
  .letterhead .date { position: absolute; left: 47px; top: 527px; font-size: 10.5px; }
  .letterhead .signature { position: absolute; left: 366px; top: 490px; width: 95px; height: 62px; background: linear-gradient(135deg, #f4f4f4, #e8e8e8); border-radius: 4px; }
  .letterhead .signatory { position: absolute; right: 35px; top: 558px; font-size: 10px; }
  .letterhead .footer { position: absolute; left: 26px; right: 0; top: 641px; text-align: center; font-size: 9.6px; white-space: nowrap; }
  .letterhead .footer span { margin: 0 5px; }
</style>
</head>
<body>

<svg width="0" height="0" style="position:absolute">
  <defs>
    <symbol id="i-pin" viewBox="0 0 16 16"><path d="M8 1a5 5 0 0 0-5 5c0 3.5 5 8 5 8s5-4.5 5-8a5 5 0 0 0-5-5zm0 7a2 2 0 1 1 0-4 2 2 0 0 1 0 4z"/></symbol>
    <symbol id="i-phone" viewBox="0 0 16 16"><circle cx="8" cy="8" r="7.5"/><path d="M5 4.5l1.5-.5 1 2-1 .8a5 5 0 0 0 2.7 2.7l.8-1 2 1-.5 1.5c-3.8 0-6.5-2.7-6.5-6.5z" fill="#fff"/></symbol>
    <symbol id="i-mail" viewBox="0 0 16 16"><circle cx="8" cy="8" r="7.5"/><rect x="4" y="5.2" width="8" height="5.6" fill="#fff"/><path d="M4 5.2l4 3 4-3" stroke="#333" stroke-width=".8" fill="none"/></symbol>
    <symbol id="i-web" viewBox="0 0 16 16"><circle cx="8" cy="8" r="7" fill="none" stroke="currentColor" stroke-width="1.3"/><path d="M1 8h14M8 1c-3 3.5-3 10.5 0 14M8 1c3 3.5 3 10.5 0 14" fill="none" stroke="currentColor" stroke-width="1"/></symbol>
  </defs>
</svg>

<!-- Business card front -->
<section class="piece card-front" aria-label="Business card front">
  <div class="panel-light"><div class="mark-square"></div></div>
  <div class="panel-dark">
    <div class="wordmark"><span class="name">GREYMARSH</span><span class="sub">CONTRACTS</span></div>
    <p class="person">Kelvan Joshi</p>
    <p class="role">(Designated Partner)</p>
    <ul class="contacts">
      <li><svg class="icon"><use href="#i-phone"/></svg>+91 97415 60382</li>
      <li><svg class="icon"><use href="#i-mail"/></svg>kelvanjoshi@mailbrook.example</li>
      <li><svg class="icon"><use href="#i-web"/></svg>www.greymarshcontracts.example</li>
    </ul>
  </div>
</section>

<!-- Business card back -->
<section class="piece card-back" aria-label="Business card back">
  <div class="mark-square"></div>
  <div class="address-band">Block No.317, Wing C, Tulvo Trade Court, Manek Pural<br>Road, Ruparel Industrial Estate, Goregaon(E), Mumbai - 400 063</div>
</section>

<!-- Envelope back -->
<section class="piece envelope-back" aria-label="Envelope back">
  <div class="flap"></div>
  <div class="wordmark"><span class="name">GREYMARSH</span><span class="sub">CONTRACTS</span></div>
</section>

<!-- Envelope front -->
<section class="piece envelope-front" aria-label="Envelope front">
  <div class="stripe"></div>
  <div class="mark-square"></div>
  <div class="wordmark"><span class="name">GREYMARSH</span><span class="sub">CONTRACTS</span></div>
  <p class="address"><svg class="icon"><use href="#i-pin"/></svg><span>Block No.317, Wing C, Tulvo Trade Court,<br>Manek Pural Road, Ruparel Industrial Estate,<br>Goregaon(E), Mumbai - 400 063</span></p>
</section>

<!-- Letterhead -->
<section class="piece letterhead" aria-label="Letterhead">
  <div class="stripe"></div>
  <div class="mark-square"></div>
  <div class="wordmark"><span class="name">GREYMARSH</span><span class="sub">CONTRACTS</span></div>
  <p class="address"><svg class="icon"><use href="#i-pin"/></svg><span>Block No.317, Wing C, Tulvo Trade Court,<br>Manek Pural Road, Ruparel Industrial Estate,<br>Goregaon(E), Mumbai - 400 063</span></p>

  <p class="greeting">Dear Mr.Kelvan</p>
  <div class="body">
    <p>Lorem ipsum dolor sit amet, consectetuer adipiscing elit, sed diam nonummy nibh euismod tincidunt ut laoreet dolore magna aliquam erat volutpat. Ut wisi enim ad minim veniam, quis nostrud exerci tation ullamcorper suscipit lobortis nisl ut aliquip ex ea commodo consequat. Duis autem vel eum iriure dolor in hendrerit in vulputate velit esse molestie consequat, vel illum dolore eu feugiat nulla facilisis at vero eros et accumsan et iusto odio dignissim qui blandit praesent luptatum zzril delenit augue duis dolore te feugait nulla facilisi.</p>
    <p class="tight">Lorem ipsum dolor sit amet, cons ectetuer adipiscing elit, sed diam nonummy nibh euismod tincidunt ut laoreet dolore magna aliquam erat volutpat. Ut wisi enim ad minim veniam, quis nostrud exerci tation ullamcorper suscipit lobortis nisl ut aliquip ex ea commodo consequat.</p>
    <p class="tight">Lorem ipsum dolor sit amet, consectetuer adipiscing elit, sed diam nonummy nibh euismod tincidunt ut laoreet dolore magna aliquam erat</p>
    <p class="gap">Lorem ipsum dolor sit amet, cons ectetuer adipiscing elit, sed diam nonummy nibh euismod tincidunt ut laoreet dolore magna aliquam erat volutpat. Ut wisi enim ad minim veniam, quis nostrud exerci tation ullamcorper suscipit lobortis nisl ut aliquip ex ea commodo consequat. Lorem ipsum dolor sit zamet, consectetuer adipiscing elit, sed diam nonummy nibh euismod tincidunt ut laoreet dolore magna aliquam erat volutpat. Ut wisi enim ad minim veniam, quis nostrud exerci tation ullamcorper suscipit lobortis nisl ut aliquip ex ea commodo consequat. Duis autem vel eum iriure dolor in hendrerit in vulputate velit esse molestie consequat, vel illum dolore eu feugiat nulla facilisis at vero eros et accumsan et iusto odio dignissim qui blandit praesent luptatum zzril delenit augue duis dolore te feugait nulla facilisi. Lorem ipsum dolor sit amet, cons ectetuer adipiscing elit, sed diam nonummy nibh euismod tincidunt ut laoreet dolore magna aliquam erat volutpat. Ut wisi enim ad minim veniam, quis nostrud exerci tation ullamcorper suscipit lobortis nisl ut aliquip ex ea commodo consequat.</p>
    <p class="gap2">Lorem ipsum dolor sit amet, cons ectetuer adipiscing elit, sed diam nonummy nibh euismod tincidunt ut laoreet dolore magna aliquam erat volutpat</p>
  </div>
  <p class="date">25th August 2022</p>
  <div class="signature" role="img" aria-label="Handwritten signature of the managing director"></div>
  <p class="signatory">Managing Director</p>
  <p class="footer">
    <span><svg class="icon"><use href="#i-phone"/></svg>+91-22-28754193</span>
    <span><svg class="icon"><use href="#i-mail"/></svg>kelvanjoshi@mailbrook.example</span>
    <span><svg class="icon"><use href="#i-web"/></svg>www.greymarshcontracts.example</span>
  </p>
</section>

</body>
</html>
```